Every Shelf Set Neatly or ESN Organized needs a business card design. ESN Organized is a professi

We need a business card design that is clean, sharp and conveys a sense of organization. I already have a logo.

Target Market(s)

Families (specifically mothers), small business owners, parents, seniors

Industry/Entity Type

Business

Contact Information for Business Card

My website is www.esnorganized-example.com and my Facebook page is http://www.sociallink-example.com/everyshelfsetneatly. The phone number is 418-552-7094 and I want to be listed as Lorna M. Pelham, Owner

Requirements
Must have
• My logo.

```html
<!DOCTYPE html>
<html lang="en">
<head>
<meta charset="utf-8">
<title>ESN Organized — Business Card</title>
<link rel="stylesheet" href="https://fonts.googleapis.com/css2?family=Roboto:wght@300;400&display=swap">
<style>
  :root {
    --page: #e9eaec;
    --card: #f7f7f7;
    --ink: #1d1d1f;
    --brand-blue: #2f7fc4;
    --band-blue: #2a78bd;
    --band-text: #ffffff;
  }
  html, body {
    margin: 0;
    width: 1200px;
    height: 1022px;
    overflow: hidden;
    background: var(--page);
    font-family: "Roboto", Arial, sans-serif;
  }
  .card {
    position: absolute;
    left: 100px;
    top: 225px;
    width: 1000px;
    height: 572px;
    background: var(--card);
    box-shadow: 0 10px 30px rgba(0,0,0,0.18);
    overflow: hidden;
  }
  .brand {
    position: absolute;
    left: 90px;
    top: 190px;
    display: flex;
    align-items: center;
    gap: 22px;
  }
  .brand-mark {
    width: 26px;
    height: 26px;
    background: var(--brand-blue);
  }
  .brand-name {
    font-weight: 300;
    font-size: 54px;
    letter-spacing: 6px;
    color: var(--ink);
    white-space: nowrap;
  }
  .person {
    position: absolute;
    right: 70px;
    top: 300px;
    text-align: right;
  }
  .person-name {
    font-weight: 400;
    font-size: 40px;
    color: var(--brand-blue);
    line-height: 1.1;
  }
  .person-role {
    font-weight: 400;
    font-size: 22px;
    color: var(--ink);
    margin-top: 4px;
  }
  .contact-band {
    position: absolute;
    left: 0;
    bottom: 0;
    width: 1000px;
    height: 150px;
  }
  .contact-list {
    position: absolute;
    left: 330px;
    bottom: 22px;
    margin: 0;
    padding: 0;
    list-style: none;
    color: var(--band-text);
    font-size: 23px;
    line-height: 34px;
  }
  .contact-list li {
    display: flex;
    align-items: center;
    gap: 12px;
  }
  .contact-icon {
    width: 16px;
    height: 16px;
    flex: none;
  }
</style>
</head>
<body>
  <div class="card">
    <div class="brand">
      <span class="brand-mark"></span>
      <span class="brand-name">Every Shelf Set Neatly</span>
    </div>

    <div class="person">
      <div class="person-name">Lorna M. Pelham</div>
      <div class="person-role">Owner</div>
    </div>

    <svg class="contact-band" viewBox="0 0 1000 150" aria-hidden="true">
      <polygon points="360,0 1000,0 1000,150 290,150" fill="var(--band-blue)"/>
    </svg>

    <ul class="contact-list">
      <li>
        <svg class="contact-icon" viewBox="0 0 16 16" aria-hidden="true">
          <path d="M3 1.5 L6 1.5 L7 5 L5.3 6.3 Q6.8 9.4 9.7 10.7 L11 9 L14.5 10 L14.5 13 Q14.5 14.5 13 14.5 Q2 13.5 1.5 3 Q1.5 1.5 3 1.5 Z" fill="#fff"/>
        </svg>
        418-552-7094
      </li>
      <li>
        <svg class="contact-icon" viewBox="0 0 16 16" aria-hidden="true">
          <circle cx="8" cy="8" r="6.5" fill="none" stroke="#fff" stroke-width="1.4"/>
          <ellipse cx="8" cy="8" rx="2.8" ry="6.5" fill="none" stroke="#fff" stroke-width="1.2"/>
          <line x1="1.5" y1="8" x2="14.5" y2="8" stroke="#fff" stroke-width="1.2"/>
        </svg>
        www.esnorganized-example.com
      </li>
      <li>
        <svg class="contact-icon" viewBox="0 0 16 16" aria-hidden="true">
          <circle cx="8" cy="8" r="6" fill="#fff"/>
        </svg>
        www.sociallink-example.com/everyshelfsetneatly
      </li>
    </ul>
  </div>
</body>
</html>
```